Consulting company business cards

We have a base design, but would be willing to update. We have a new logo/"tag" that needs to be added. Current business card design is attached for reference into our "style."

Industry/Entity Type

Business

Contact Information for Business Card

Should contain name and title, office number, mobile number if appropriate, e-mail, website, physical address, and company logo.

Font styles to use
Other font styles liked:
• See current card design on KorvandBCard

Colors
0455a3
85acd3
aaaaaa

Requirements
Must have
• Our colors are navy blue, gray, and a lighter blue
Nice to have
• Design that I can easily drop in new names/titles as we hire employees.

```html
<!DOCTYPE html>
<html lang="en">
<head>
<meta charset="utf-8">
<title>Teramoor Business Card</title>
<link href="https://fonts.googleapis.com/css2?family=Libre+Franklin:wght@300;400;500;700&display=swap" rel="stylesheet">
<style>
  :root {
    --backdrop: #3a322e;
    --card: #141517;
    --card-edge: #1d1f22;
    --navy: #0455a3;
    --navy-deep: #0f3f6e;
    --light-blue: #85acd3;
    --slate-blue: #6b8fa8;
    --gray: #aaaaaa;
    --white: #f2f2f2;
  }
  * { box-sizing: border-box; margin: 0; padding: 0; }
  html, body { width: 1200px; height: 864px; overflow: hidden; }
  body {
    background: var(--backdrop);
    font-family: "Libre Franklin", Arial, sans-serif;
    position: relative;
  }
  .card {
    position: absolute;
    width: 510px;
    height: 291px;
    background: linear-gradient(160deg, var(--card-edge), var(--card));
    border-radius: 3px;
    box-shadow: 0 10px 30px rgba(0,0,0,.45);
    overflow: hidden;
  }
  /* Front */
  .card-front { left: 60px; top: 180px; }
  .front-mark {
    position: absolute;
    left: 0; right: 0; top: 88px;
    display: flex; align-items: center; justify-content: center; gap: 14px;
  }
  .front-mark .dot {
    width: 34px; height: 34px; border-radius: 50%;
    background: var(--slate-blue);
  }
  .front-mark .wordmark {
    font-weight: 700; font-size: 48px; letter-spacing: 2px;
    color: var(--slate-blue); text-transform: uppercase;
  }
  .front-url {
    position: absolute; left: 34px; bottom: 40px;
    font-size: 13px; letter-spacing: 6px; color: var(--gray);
  }
  /* Back */
  .card-back { left: 630px; top: 393px; }
  .brand {
    position: absolute; left: 26px; top: 108px;
  }
  .brand-row { display: flex; align-items: center; gap: 8px; }
  .brand .wordmark {
    font-weight: 700; font-size: 34px; letter-spacing: 1px;
    color: var(--navy); text-transform: uppercase; line-height: 1;
  }
  .brand .dot {
    width: 20px; height: 20px; border-radius: 50%;
    background: var(--light-blue);
  }
  .brand .tagline {
    margin-top: 6px; font-size: 9.5px; letter-spacing: .8px;
    color: var(--gray); text-transform: uppercase;
  }
  .divider {
    position: absolute; left: 255px; top: 40px; width: 1px; height: 211px;
    background: linear-gradient(to bottom, transparent, #8a8a8a 50%, transparent);
  }
  .contact {
    position: absolute; left: 275px; top: 50px; right: 16px;
    color: var(--white); font-size: 12.5px; line-height: 1.35;
  }
  .contact .name { font-size: 18px; color: var(--navy); font-weight: 500; }
  .contact .title { font-size: 14px; color: var(--light-blue); margin-bottom: 14px; }
  .contact .address { margin-bottom: 10px; }
  .contact ul { list-style: none; }
  .contact li { display: flex; align-items: center; gap: 9px; height: 20px; white-space: nowrap; }
  .contact svg { width: 12px; height: 12px; flex: none; fill: var(--navy-deep); }
</style>
</head>
<body>
  <section class="card card-front">
    <div class="front-mark">
      <span class="dot"></span>
      <span class="wordmark">Teramoor</span>
    </div>
    <p class="front-url">www.teramoortech.com</p>
  </section>

  <section class="card card-back">
    <div class="brand">
      <div class="brand-row">
        <span class="wordmark">Teramoor</span>
        <span class="dot"></span>
      </div>
      <p class="tagline">A Cloud Consulting Company</p>
    </div>
    <div class="divider"></div>
    <div class="contact">
      <p class="name">Marenkorvand</p>
      <p class="title">Office Manager</p>
      <p class="address">1180 W 48th ST<br>Fairmont Indiana 46310</p>
      <ul>
        <li><svg viewBox="0 0 12 12"><path d="M2.5 1h2l1 2.6-1.3 1a6 6 0 0 0 2.7 2.7l1-1.3L11 7v2a1.2 1.2 0 0 1-1.3 1.2A9 9 0 0 1 1.3 2.3 1.2 1.2 0 0 1 2.5 1z"/></svg>555.014.3806</li>
        <li><svg viewBox="0 0 12 12"><rect x="3" y="0.5" width="6" height="11" rx="1"/></svg>555.014.3852</li>
        <li><svg viewBox="0 0 12 12"><path d="M1 2.5h10v7H1z M1.5 3l4.5 3.5L10.5 3" stroke="#141517" stroke-width=".8"/></svg>mkorvand@teramoortech.com</li>
        <li><svg viewBox="0 0 12 12"><circle cx="6" cy="6" r="5.5"/></svg>www.teramoortech.com</li>
      </ul>
    </div>
  </section>
</body>
</html>
```